RW Framewell Inc Business cards

We need business cards using our existing logo but slightly modified. Right now the logo says RW Loadbearing Masonry. We want to keep the RW part of the design, but replace the Structural Concrete portion with "FRAMEWELL". Please see the attached file.
Ideally this would be a blank template so we can add Different Names, titles, and phone numbers later.
On the one side we want only the logo and on the other side the detail. I'm attaching an example for you to see.
Please reach out with any other questions. Our address and other details will be given out once we find a design we like.

Target Market(s)

Construction Industry

```html
<!DOCTYPE html>
<html lang="en">
<head>
<meta charset="utf-8">
<title>RW Framewell Inc Business Cards</title>
<link rel="stylesheet" href="https://fonts.googleapis.com/css2?family=Open+Sans:wght@400;600;700&display=swap">
<style>
  :root {
    --bg: #5b80ba;
    --brand-blue: #2f63ab;
    --brand-blue-deep: #23508f;
    --card-white: #f7f7f5;
    --swoosh-grey: #6f6f71;
    --text-grey: #5a5a5c;
    --text-white: #ffffff;
  }
  * { box-sizing: border-box; margin: 0; padding: 0; }
  html, body {
    width: 1200px; height: 852px; overflow: hidden;
    background: var(--bg);
    font-family: "Open Sans", Arial, sans-serif;
  }
  .canvas {
    position: relative; width: 1200px; height: 852px;
    display: flex; align-items: center; justify-content: center; gap: 60px;
  }
  .card {
    position: relative; width: 510px; height: 300px;
    border-radius: 22px; overflow: hidden;
    box-shadow: 0 6px 14px rgba(20, 40, 80, 0.35);
  }
  /* Logo side */
  .card--back {
    background: var(--brand-blue);
    display: flex; align-items: center; justify-content: center;
  }
  .wordmark {
    color: var(--brand-blue-deep); font-weight: 600; text-align: center; line-height: 1;
  }
  .wordmark__initials { display: block; font-size: 96px; letter-spacing: 2px; }
  .wordmark__name { display: block; font-size: 30px; letter-spacing: 8px; margin-top: 6px; }

  /* Detail side */
  .card--front { background: var(--card-white); }
  .card__wave { position: absolute; inset: 0; width: 100%; height: 100%; }
  .card--front .wordmark {
    position: absolute; top: 20px; right: 34px; color: var(--brand-blue);
  }
  .card--front .wordmark__initials { font-size: 56px; }
  .card--front .wordmark__name { font-size: 17px; letter-spacing: 5px; margin-top: 4px; }
  .person { position: absolute; left: 32px; top: 132px; }
  .person__name { color: var(--brand-blue); font-weight: 700; font-size: 19px; }
  .person__title { color: var(--text-grey); font-size: 12.5px; margin-top: 1px; }
  .address {
    position: absolute; left: 32px; top: 192px;
    color: var(--text-grey); font-size: 12.5px; line-height: 1.45; font-style: normal;
  }
  .contact {
    position: absolute; right: 22px; top: 158px; list-style: none;
    color: var(--text-white); font-size: 12.5px; line-height: 20px; text-align: right;
  }
  .contact li { display: flex; align-items: center; justify-content: flex-end; gap: 6px; }
  .contact svg { width: 11px; height: 11px; fill: var(--text-white); }
</style>
</head>
<body>
<main class="canvas">
  <section class="card card--back" aria-label="Card logo side">
    <div class="wordmark">
      <span class="wordmark__initials">RW</span>
      <span class="wordmark__name">FRAMEWELL</span>
    </div>
  </section>

  <section class="card card--front" aria-label="Card detail side">
    <svg class="card__wave" viewBox="0 0 510 300" preserveAspectRatio="none" aria-hidden="true">
      <path d="M0,300 L0,282 C130,276 240,260 300,195 C345,148 410,130 510,126 L510,300 Z" fill="var(--brand-blue)"/>
      <path d="M30,270 C130,262 230,245 290,185 C335,138 405,114 510,110 L510,119 C410,123 352,144 306,191 C250,250 140,266 30,270 Z" fill="var(--swoosh-grey)"/>
    </svg>

    <div class="wordmark">
      <span class="wordmark__initials">RW</span>
      <span class="wordmark__name">FRAMEWELL</span>
    </div>

    <div class="person">
      <p class="person__name">Dale RW Harmon</p>
      <p class="person__title">Managing Director</p>
    </div>

    <address class="address">87 Quarry Lane, Millbrook,<br>Oregon, US 970512</address>

    <ul class="contact">
      <li>555-014-2290
        <svg viewBox="0 0 24 24"><path d="M6.6 10.8a15 15 0 0 0 6.6 6.6l2.2-2.2a1 1 0 0 1 1-.25 11.4 11.4 0 0 0 3.6.57 1 1 0 0 1 1 1V20a1 1 0 0 1-1 1A17 17 0 0 1 3 4a1 1 0 0 1 1-1h3.5a1 1 0 0 1 1 1c0 1.250.2 2.450.57 3.57a1 1 0 0 1-.25 1z"/></svg>
      </li>
      <li>framewellbuild.com
        <svg viewBox="0 0 24 24"><path d="M2 5h20v14H2z M4 7v.5l8 5 8-5V7z" fill-rule="evenodd"/></svg>
      </li>
      <li>dale@framewellbuild.com
        <svg viewBox="0 0 24 24"><circle cx="12" cy="12" r="10"/></svg>
      </li>
    </ul>
  </section>
</main>
</body>
</html>
```